Chiropractic Business Card

I need a business card designed to help me stand apart from my competition. I really like simple, clean designs that appear open and inviting. I would like the designs to incorporate the color blue, green, or both. I really like the attached picture because it highlights that I just don't treat "back pain" and it being a nice computer graphic helps show that I have a modern practice. "Modern practice" meaning merging technology and most current research in my patient care.

My information is:

Lyle Farwick, DC
Phone- (707) 555-0182
Email- drlylefarwick@mailnest.example
Website- www.brevincourtchiropractic.example
Address- 248 Tolliver Street, Sonoma, CA 95999

Jpeg and pdf attached of Brevincourt Chiropractic logo.
Updates

Atmosphere to be clean lines and solid colors to be have gradient fading, but don't want too much going on with the fading. Simple.

Target Market(s)

Active adults who are health conscious between the ages of 20-70

Industry/Entity Type

Computer

Colors
0455a3
85cae6

Requirements
Must have
• Change color of Brevincourt chiropractic logo (maroon) to fit the rest of the design.
Nice to have
• Can separate the running image from the black background to have it work with the design.

```html
<!DOCTYPE html>
<html lang="en">
<head>
<meta charset="utf-8">
<title>Brevincourt Chiropractic – Business Card</title>
<link rel="stylesheet" href="https://fonts.googleapis.com/css2?family=Jost:wght@400;600&display=swap">
<style>
  :root {
    --page: #e9e9e7;
    --card: #f3f3f2;
    --blue: #0455a3;
    --green: #5fa83a;
    --ink: #3c3c3c;
    --ink-soft: #6a6a6a;
    --figure-a: #85cae6;
    --figure-b: #2f6f9a;
  }
  * { box-sizing: border-box; margin: 0; padding: 0; }
  html, body { width: 1200px; height: 900px; overflow: hidden; }
  body {
    background: var(--page);
    font-family: "Jost", sans-serif;
    color: var(--ink);
    position: relative;
  }
  .card {
    position: absolute;
    left: 320px;
    width: 560px;
    height: 320px;
    background: var(--card);
    box-shadow: 0 6px 18px rgba(0,0,0,.12);
    overflow: hidden;
  }
  .card--front { top: 70px; }
  .card--back { top: 500px; }

  .brand {
    display: flex;
    align-items: center;
    gap: 8px;
    font-weight: 600;
    color: var(--green);
    text-transform: uppercase;
    line-height: 1.05;
  }
  .brand__mark {
    width: 10px; height: 10px;
    background: var(--green);
    flex: none;
  }

  /* front */
  .runner-art {
    position: absolute;
    left: 70px; top: 18px;
    width: 230px; height: 290px;
    border-radius: 40% 45% 30% 35%;
    background: radial-gradient(ellipse at 50% 45%, var(--figure-a), var(--figure-b) 70%, rgba(47,111,154,0) 72%);
    opacity: .85;
  }
  .card--front .brand {
    position: absolute;
    left: 315px; top: 128px;
    font-size: 21px;
    width: 220px;
  }

  /* back */
  .card--back .brand {
    position: absolute;
    left: 34px; top: 40px;
    font-size: 20px;
    width: 230px;
  }
  .edge-band {
    position: absolute;
    left: 0; bottom: 0;
    width: 100%; height: 9px;
    display: flex;
  }
  .edge-band__blue { width: 40%; background: var(--blue); }
  .edge-band__green { width: 60%; background: var(--green); }

  .contact {
    position: absolute;
    left: 268px; top: 92px;
    width: 270px;
  }
  .contact__name {
    font-weight: 600;
    font-size: 14px;
    letter-spacing: .22em;
    text-transform: uppercase;
    color: var(--ink);
    margin-bottom: 14px;
  }
  .contact__list { list-style: none; }
  .contact__item {
    display: flex;
    align-items: flex-start;
    gap: 10px;
    font-size: 10.5px;
    letter-spacing: .12em;
    text-transform: uppercase;
    color: var(--ink-soft);
    line-height: 1.5;
    margin-bottom: 6px;
  }
  .contact__icon { flex: none; width: 12px; height: 12px; margin-top: 2px; }
  .contact__icon * { fill: var(--blue); }
</style>
</head>
<body>

<section class="card card--front">
  <div class="runner-art" role="img" aria-label="Translucent blue anatomical runner figure with highlighted joints"></div>
  <div class="brand"><span class="brand__mark"></span><span>Brevincourt Chiropractic Offices Inc.</span></div>
</section>

<section class="card card--back">
  <div class="brand"><span class="brand__mark"></span><span>Brevincourt Chiropractic Offices Inc.</span></div>

  <div class="contact">
    <p class="contact__name">Lyle Farwick, DC</p>
    <ul class="contact__list">
      <li class="contact__item">
        <svg class="contact__icon" viewBox="0 0 12 12"><path d="M6 0a4 4 0 0 0-4 4c0 3 4 8 4 8s4-5 4-8a4 4 0 0 0-4-4zm0 5.6A1.6 1.6 0 1 1 6 2.4a1.6 1.6 0 0 1 0 3.2z"/></svg>
        <span>Address: 248 Tolliver Street, Sonoma, CA 95999</span>
      </li>
      <li class="contact__item">
        <svg class="contact__icon" viewBox="0 0 12 12"><path d="M2.5 0.5l2 2.5-1.2 1.4a7 7 0 0 0 4.3 4.3L9 7.5l2.5 2-1.3 2A9.5 9.5 0 0 1 .5 1.8z"/></svg>
        <span>(707) 555-0182</span>
      </li>
      <li class="contact__item">
        <svg class="contact__icon" viewBox="0 0 12 12"><path d="M0 2h12v8H0zm1 1v.4l5 3.3 5-3.3V3zm0 1.6V9h10V4.6L6 8z"/></svg>
        <span>drlylefarwick@mailnest.example</span>
      </li>
      <li class="contact__item">
        <svg class="contact__icon" viewBox="0 0 12 12"><path d="M6 0a6 6 0 1 0 0 12A6 6 0 0 0 6 0zm0 1.2c.8.9 1.3 2.2 1.5 3.6h-3C4.7 3.4 5.2 2.1 6 1.2zM1.3 5.8h2.2c0 1.5.5 3 1.2 4A4.8 4.8 0 0 1 1.3 5.8zm3.2 0h3c-.1 1.5-.6 2.8-1.5 3.8-.9-1-1.4-2.3-1.5-3.8zm4 0h2.2a4.8 4.8 0 0 1-3.4 4c.7-1 1.2-2.5 1.2-4zM1.3 4.8a4.8 4.8 0 0 1 3.4-3.6c-.7 1-1.1 2.2-1.2 3.6zm7.2 0c-.1-1.4-.5-2.6-1.2-3.6a4.8 4.8 0 0 1 3.4 3.6z"/></svg>
        <span>www.brevincourtchiropractic.example</span>
      </li>
    </ul>
  </div>

  <div class="edge-band"><span class="edge-band__blue"></span><span class="edge-band__green"></span></div>
</section>

</body>
</html>
```